Business Card Design

We need a business card designed for our new company. Prefer a black card with white logo & writing.

Contact Information for Business Card

Ted Galloway, address: 7-4812 Fernhollow Road, Abbotsford, BC, V3K 8R2, Office Phone: 604-712-3390, Cell: 604-947-2164, Email: ted@resinworkshub.ca

Colors

Designer to choose only greyscale colors for use in the design.

```html
<!DOCTYPE html>
<html lang="en">
<head>
<meta charset="utf-8">
<title>Resin Works Hub – Business Card</title>
<link rel="stylesheet" href="https://fonts.googleapis.com/css2?family=Montserrat:wght@300;400;600&display=swap">
<style>
  :root {
    --backdrop: #1e1e1e;
    --card: #000000;
    --ink: #ffffff;
  }
  * { margin: 0; padding: 0; box-sizing: border-box; }
  html, body {
    width: 1200px; height: 900px; overflow: hidden;
    background: var(--backdrop);
    font-family: "Montserrat", sans-serif;
    color: var(--ink);
  }
  .canvas { position: relative; width: 1200px; height: 900px; }
  .card {
    position: absolute; top: 192px;
    width: 296px; height: 518px;
    background: var(--card);
  }
  .card--front { left: 292px; }
  .card--back { left: 614px; }

  .wordmark {
    position: absolute; left: 0; right: 0;
    text-align: center;
    font-weight: 600;
    font-size: 25px;
    line-height: 1.1;
    letter-spacing: 0.04em;
    color: var(--ink);
  }
  .card--front .wordmark { top: 86px; }
  .card--back .wordmark { top: 230px; }

  .holder-name {
    position: absolute; left: 49px; top: 448px;
    position: absolute;
    font-weight: 300; font-size: 28px; letter-spacing: 0.05em;
    text-transform: uppercase;
  }
  .card--front .holder-name { top: 256px; }

  .contact-list { position: absolute; left: 47px; top: 330px; list-style: none; }
  .contact-item {
    display: flex; align-items: center;
    margin-bottom: 18px;
  }
  .contact-icon { width: 24px; height: 27px; margin-right: 12px; flex: none; }
  .contact-text { font-weight: 400; font-size: 13px; line-height: 18px; }

  .site-url {
    position: absolute; left: 0; right: 0; top: 472px;
    text-align: center;
    font-size: 13px; letter-spacing: 0.22em; font-weight: 300;
  }
  .site-url strong { font-weight: 600; }
</style>
</head>
<body>
<main class="canvas">
  <section class="card card--front">
    <div class="wordmark">RESIN WORKS<br>HUB</div>
    <h1 class="holder-name">Ted Galloway</h1>
    <ul class="contact-list">
      <li class="contact-item">
        <svg class="contact-icon" viewBox="0 0 24 27" aria-hidden="true">
          <polygon points="12,0 24,6.75 24,20.25 12,27 0,20.25 0,6.75" fill="#fff"/>
          <path d="M12 6.5a5 5 0 0 0-5 5c0 3.8 5 9 5 9s5-5.2 5-9a5 5 0 0 0-5-5z" fill="#000"/>
          <circle cx="12" cy="11.5" r="1.9" fill="#fff"/>
        </svg>
        <p class="contact-text">7-4812 Fernhollow Road<br>Abbotsford, BC, V3K 8R2</p>
      </li>
      <li class="contact-item">
        <svg class="contact-icon" viewBox="0 0 24 27" aria-hidden="true">
          <polygon points="12,0 24,6.75 24,20.25 12,27 0,20.25 0,6.75" fill="#fff"/>
          <path d="M8.2 7.5l2.3-.4 1.3 3-1.5 1.2c.7 1.6 1.9 2.8 3.4 3.5l1.2-1.5 3 1.3-.4 2.3c-.2.8-1 1.3-1.8 1.2-4.3-.6-7.6-3.9-8.3-8.3-.1-.8.4-1.5 1.2-1.8z" fill="#000"/>
        </svg>
        <p class="contact-text">604-712-3390<br>604-947-2164</p>
      </li>
      <li class="contact-item">
        <svg class="contact-icon" viewBox="0 0 24 27" aria-hidden="true">
          <polygon points="12,0 24,6.75 24,20.25 12,27 0,20.25 0,6.75" fill="#fff"/>
          <rect x="5.5" y="9" width="13" height="9" fill="#000"/>
          <path d="M6 9.5l6 4.5 6-4.5" fill="none" stroke="#fff" stroke-width="1.2"/>
        </svg>
        <p class="contact-text">ted@resinworkshub.ca<br>www.resinworkshub.ca</p>
      </li>
    </ul>
  </section>

  <section class="card card--back">
    <div class="wordmark">RESIN WORKS<br>HUB</div>
    <p class="site-url">www.<strong>resinworkshub</strong>.ca</p>
  </section>
</main>
</body>
</html>
```